Brightway Haus Inc. Business Card Design

Brightway Haus Inc. is in search of a great clean design for our business cards!

Looking to incorporate our full logo and watermark on side one (however, I am open to having the text and watermark separated within the design.)

On side two, I am looking to have contact information (Name, Position, Phone #, Email, Website (www.thebrightwayhaus.ca). Can have the logo and/or watermark as part of the design if applicable.

Please add tagline "Where Shine Counts" on either side 1 or 2. This tagline can be in a sans serif, serif or cursive font as long as it compliments overall design. Capitalization can be title or sentence case depending on how it fits within the design.

Get creative!! Looking for a clean, crisp, premium design! Looking for a glossy card finish with spot UV features when printed. Cards will also be printed with rounded corners. Standard dimensions (3.5 x 2).

Target Market(s)

B2B - primary clients are business owners or property management corporations. (residential jobs are few and far between)

Industry/Entity Type

Business

Contact Information for Business Card

- clean, crisp design
- double sided
- spot UV accents and glossy finish upon printing
- standard business card size (3.5 x 2) with rounded corners
- please see project description for requirements per side

Font styles to use
Sans Serif

Requirements
Must have
• - adequate bleeds with print ready files
• - cohesive design elements between side 1 & 2
• - spot UV elements (can be on both sides or just one, use your discretion)
• - colour pallet should match the logo file provided
• - incorporate tagline "where shine counts" (this tagline can be in a serif or sans serif font as long as it is complimentary to the overall design.
Nice to have
• - Premium elements with a clean design
Should not have
• - Please omit cartoon or whimsical like designs, think premium.
• - Colours should not stray from the pallet of the provided logo.

```html
<!DOCTYPE html>
<html lang="en">
<head>
<meta charset="utf-8">
<title>Brightway Haus Inc. Business Cards</title>
<link href="https://fonts.googleapis.com/css2?family=Open+Sans:wght@700;800&family=Roboto:wght@400;500&family=Roboto+Condensed:wght@400;500&display=swap" rel="stylesheet">
<style>
  :root {
    --navy: #1b2555;
    --teal: #12b9bd;
    --grey: #b3b3b3;
    --ink: #4a4a4a;
    --paper: #ffffff;
    --backdrop: #ebe6df;
  }
  html, body {
    margin: 0;
    padding: 0;
    width: 1200px;
    height: 960px;
    overflow: hidden;
    background: var(--backdrop);
  }
  .canvas {
    position: relative;
    width: 1200px;
    height: 960px;
  }
  .card {
    position: absolute;
    left: 320px;
    width: 600px;
    height: 343px;
    border-radius: 18px;
    overflow: hidden;
    box-shadow: 0 3px 8px rgba(0,0,0,0.25);
  }
  .card-front {
    top: 107px;
    background: var(--navy);
    color: var(--paper);
    text-align: center;
  }
  .front-name {
    position: absolute;
    left: 0; right: 0;
    top: 140px;
    font-family: "Open Sans", sans-serif;
    font-weight: 800;
    font-size: 38px;
    letter-spacing: -0.5px;
    line-height: 1;
  }
  .front-tagline {
    position: absolute;
    left: 0; right: 0;
    top: 194px;
    font-family: "Roboto", sans-serif;
    font-weight: 400;
    font-size: 15px;
    letter-spacing: 7px;
  }
  .card-back {
    top: 492px;
    background: var(--paper);
    color: var(--ink);
    font-family: "Roboto", sans-serif;
  }
  .accent-band {
    position: absolute;
    right: 0; top: 0;
    width: 118px;
    height: 100%;
    background: var(--teal);
  }
  .back-logo {
    position: absolute;
    left: 29px;
    top: 36px;
    display: flex;
    align-items: center;
    gap: 10px;
  }
  .logo-square {
    width: 26px;
    height: 26px;
    background: var(--navy);
  }
  .logo-name {
    font-family: "Open Sans", sans-serif;
    font-weight: 800;
    font-size: 27px;
    color: var(--teal);
    letter-spacing: -0.5px;
  }
  .person {
    position: absolute;
    left: 29px;
    top: 118px;
  }
  .person-name {
    font-family: "Roboto Condensed", sans-serif;
    font-weight: 500;
    font-size: 21px;
    color: var(--teal);
    margin: 0;
  }
  .person-role {
    font-family: "Roboto Condensed", sans-serif;
    font-weight: 500;
    font-size: 15px;
    color: var(--navy);
    margin: 4px 0 0;
  }
  .address {
    position: absolute;
    left: 29px;
    top: 175px;
    font-size: 14px;
    line-height: 18px;
    margin: 0;
    font-style: normal;
  }
  .contact-list {
    position: absolute;
    left: 29px;
    top: 221px;
    list-style: none;
    margin: 0;
    padding: 0;
    font-size: 14px;
    line-height: 19px;
  }
  .contact-list li {
    display: flex;
    align-items: center;
    gap: 9px;
  }
  .contact-list svg {
    width: 14px;
    height: 14px;
    fill: var(--teal);
    flex: none;
  }
</style>
</head>
<body>
<main class="canvas">
  <section class="card card-front">
    <div class="front-name">BRIGHTWAY HAUS INC.</div>
    <div class="front-tagline">Where Shine Counts</div>
  </section>

  <section class="card card-back">
    <div class="accent-band"></div>
    <div class="back-logo">
      <span class="logo-square"></span>
      <span class="logo-name">BRIGHTWAY HAUS INC.</span>
    </div>
    <div class="person">
      <p class="person-name">DANIEL MARSH</p>
      <p class="person-role">CEO/FOUNDER</p>
    </div>
    <address class="address">1420 Harbor View Road<br>Juneau, Alaska 99801</address>
    <ul class="contact-list">
      <li><svg viewBox="0 0 16 16"><path d="M3.6 1l2.3 2.6-1.4 2c.9 2 2.6 3.7 4.6 4.7l2-1.4L13.8 11l-.9 2.8c-6.3-.4-10.9-5.3-11.6-11.3z"/></svg>907 555 0142</li>
      <li><svg viewBox="0 0 16 16"><path d="M4 0h8v16H4zM5.5 2v10h5V2zM7 13.2h2v1.4H7z" fill-rule="evenodd"/></svg>907 555 0187</li>
      <li><svg viewBox="0 0 16 16"><path d="M4 1h8v4H4zM1 6h14v6h-2v3H3v-3H1zM4.5 10v3.5h7V10z" fill-rule="evenodd"/></svg>907 555 0119</li>
      <li><svg viewBox="0 0 16 16"><path d="M1 3h14v10H1zM2.5 4.5v.3L8 8.6l5.5-3.8v-.3zM2.5 6.6v5h11v-5L8 10.4z" fill-rule="evenodd"/></svg>hello@thebrightwayhaus.ca</li>
      <li><svg viewBox="0 0 16 16"><circle cx="8" cy="8" r="7"/><path d="M1 8h14M8 1c-3 3.5-3 10.5 0 14M8 1c3 3.5 3 10.5 0 14" stroke="#fff" stroke-width="1.1" fill="none"/></svg>www.thebrightwayhaus.ca</li>
    </ul>
  </section>
</main>
</body>
</html>
```